Electrical Contractor Brochure, Folder and Letter Head

Brightwell Power Ltd. is an Edmonton based electrical contractor focusing on commercial and industrial electrical services. Our target market is manufacturing facilities, warehouses and commercial buildings.

We want to seem larger than we are with service vehicles and electricians ready to dispatch to service calls and new installations. Our key color is the blue in the logo. The BWP logo is well branded in Edmonton and should be on the brochure.

We are looking for a tri-fold brochure, full-page brochure with folder sleeves and a letter head.
Updates

Please ignore the second page of copy.  I only want the electrical content in the brochure.  This is my mistake.  Please use only the first page of copy.

Industry/Entity Type

Electrical

Requirements
Must have
• Many background pics of the services, electricians and projects. I like the faded BWP logo in the background of the letterhead! Folder Size A4
Nice to have
• Try the pic named Cover Pic1 to on the front of the brochure.
Should not have
• DO NOT USE ANY WEBSITE CONTENT. THIS IS NOT OUR BUSINESS. PLEASE USE ONLY CONTENT AND COLOR FROM THE ATTACHED FILES!!

```html
<!DOCTYPE html>
<html lang="en">
<head>
<meta charset="utf-8">
<title>Brightwell Power Ltd. — Letterhead</title>
<link rel="stylesheet" href="https://fonts.googleapis.com/css2?family=Source+Sans+3:wght@400;700;900&display=swap">
<style>
  :root {
    --brand-blue: #1560ac;
    --brand-navy: #1d3f8f;
    --ink: #3a3a3a;
    --rule-grey: #4a4a4a;
    --divider: #c9c9c9;
    --paper: #ffffff;
    --watermark: #eef2f7;
    --page-bg: #ffffff;
  }
  * { box-sizing: border-box; margin: 0; padding: 0; }
  html, body {
    width: 1011px; height: 1200px; overflow: hidden;
    background: var(--page-bg);
    font-family: "Source Sans 3", "Myriad Pro", sans-serif;
  }
  .letterhead {
    position: relative;
    width: 1011px; height: 1200px;
    background: var(--paper);
    overflow: hidden;
  }
  .brand {
    position: absolute;
    left: 62px; top: 78px;
    display: flex; align-items: center; gap: 14px;
  }
  .brand-mark {
    width: 22px; height: 22px;
    background: var(--brand-blue);
  }
  .brand-name {
    font-weight: 900;
    font-size: 40px;
    letter-spacing: 0.5px;
    color: var(--brand-navy);
    line-height: 1;
  }
  .contact {
    position: absolute;
    left: 797px; top: 66px;
    height: 85px;
    border-left: 1px solid var(--divider);
    padding-left: 15px;
    list-style: none;
  }
  .contact li {
    display: flex; align-items: center; gap: 6px;
    font-size: 15px; line-height: 19px;
    color: var(--ink);
    white-space: nowrap;
  }
  .contact svg { width: 10px; height: 10px; flex: none; fill: var(--brand-blue); }
  .watermark {
    position: absolute;
    left: 0; right: 0; top: 470px;
    text-align: center;
    font-weight: 900;
    font-size: 290px;
    line-height: 1;
    letter-spacing: 10px;
    color: var(--watermark);
    user-select: none;
  }
  .footer-wave {
    position: absolute;
    left: 0; bottom: 0;
    width: 1011px; height: 130px;
  }
  .address {
    position: absolute;
    left: 85px; top: 1137px;
    font-size: 15px; line-height: 23px;
    color: #ffffff;
  }
</style>
</head>
<body>
<main class="letterhead">
  <header>
    <div class="brand">
      <span class="brand-mark"></span>
      <span class="brand-name">Brightwell Power Ltd.</span>
    </div>
    <ul class="contact">
      <li><svg viewBox="0 0 10 10"><path d="M2 0.5 L4 2.8 L3 4 Q4.5 6 6 7 L7.2 6 L9.5 8 L8 9.5 Q3 9 0.5 2Z"/></svg>780-555-0142</li>
      <li><svg viewBox="0 0 10 10"><rect x="2.5" y="0.5" width="5" height="3.5"/><rect x="0.5" y="4.5" width="9" height="5" rx="1"/></svg>780-555-0142</li>
      <li><svg viewBox="0 0 10 10"><path d="M0.5 2 H9.5 V8.5 H0.5Z M0.5 2 L5 6 L9.5 2" stroke="#fff" stroke-width="0.8"/></svg>info@brightwellpower.ca</li>
      <li><svg viewBox="0 0 10 10"><circle cx="5" cy="5" r="4.5"/><path d="M0.5 5H9.5M5 0.5V9.5" stroke="#fff" stroke-width="0.7"/></svg>www.brightwellpower.ca</li>
    </ul>
  </header>

  <div class="watermark" aria-hidden="true">BWP</div>

  <footer>
    <svg class="footer-wave" viewBox="0 0 1011 130" preserveAspectRatio="none" aria-hidden="true">
      <path d="M0,52 C250,18 480,45 650,85 C800,118 930,115 1011,108 V130 H0Z" fill="var(--brand-blue)"/>
      <path d="M0,30 C180,6 360,14 500,40" fill="none" stroke="var(--brand-blue)" stroke-width="7"/>
      <path d="M560,55 C740,100 900,96 1011,86" fill="none" stroke="var(--brand-blue)" stroke-width="6"/>
      <path d="M0,46 C250,12 480,40 650,81 C800,113 930,110 1011,102" fill="none" stroke="#ffffff" stroke-width="7"/>
      <path d="M110,10 C340,-4 550,32 700,72 C830,104 940,100 1011,94" fill="none" stroke="var(--rule-grey)" stroke-width="2"/>
    </svg>
    <address class="address" style="font-style: normal;">
      00, complex name<br>
      City, state
    </address>
  </footer>
</main>
</body>
</html>
```